New Electrical Business Card Design

I would like a new design for my business cards.
i would like the same logo and font but new design
Please see attached files for front and back design.
large image can be used for graphics.
I would like the instagram link incorporated to back of card.
website site address needs to be changed to www.kestrelhillelectrical.au
everything else stays as is

```html
<!DOCTYPE html>
<html lang="en">
<head>
<meta charset="utf-8">
<title>Kestrel Hill – Business Card</title>
<link href="https://fonts.googleapis.com/css2?family=Montserrat:wght@400;500;600;800&display=swap" rel="stylesheet">
<style>
  :root {
    --backdrop: #1e1e1e;
    --card-light: #ffffff;
    --card-dark: #2b2b2b;
    --ink: #1c1c1c;
    --ink-soft: #6d6d6d;
    --accent: #1f8a3c;
    --divider: #8a8a8a;
    --emboss: #1a1a1a;
    --on-dark: #f2f2f2;
  }
  * { margin: 0; padding: 0; box-sizing: border-box; }
  html, body { width: 1200px; height: 1059px; overflow: hidden; }
  body {
    position: relative;
    background: var(--backdrop);
    font-family: "Montserrat", sans-serif;
    color: var(--ink);
  }
  .card {
    position: absolute;
    border-radius: 22px;
    overflow: hidden;
  }
  .card-front {
    left: 256px; top: 89px; width: 688px; height: 390px;
    background: var(--card-light);
  }
  .card-back {
    left: 254px; top: 547px; width: 693px; height: 393px;
    background: var(--card-dark);
  }
  .brand {
    position: absolute;
    display: flex;
    align-items: center;
    white-space: nowrap;
  }
  .brand-name {
    font-weight: 800;
    letter-spacing: 0.5px;
    line-height: 1;
  }
  .brand-dot {
    flex: none;
    border-radius: 50%;
    background: var(--accent);
  }
  .card-front .brand {
    left: 40px; top: 178px;
    gap: 8px;
  }
  .card-front .brand-name { font-size: 32px; color: var(--ink); }
  .card-front .brand-dot { width: 12px; height: 12px; }

  .divider {
    position: absolute;
    left: 344px; top: 113px;
    width: 1px; height: 166px;
    background: var(--divider);
  }
  .contact-block {
    position: absolute;
    left: 371px; top: 106px;
  }
  .person-name {
    font-size: 20px; font-weight: 600;
    letter-spacing: 0.6px;
    color: var(--ink-soft);
    margin-bottom: 16px;
  }
  .person-name .first { color: var(--accent); font-weight: 800; }
  .contact-list { list-style: none; }
  .contact-list li {
    display: flex; align-items: center; gap: 6px;
    font-size: 17px; font-weight: 400;
    height: 26.5px;
  }
  .contact-list svg { width: 14px; height: 14px; flex: none; margin-right: 1px; }
  .registration {
    margin-top: 16px;
    font-size: 17px; line-height: 22px;
  }
  .services {
    position: absolute;
    left: 0; right: 0; top: 331px;
    text-align: center;
    font-size: 17px; font-weight: 600;
  }
  .services .sep { color: var(--accent); margin: 0 4px; }

  .card-back .brand {
    left: 0; right: 0; top: 160px;
    justify-content: center;
    gap: 12px;
  }
  .card-back .brand-name {
    font-size: 60px;
    color: var(--emboss);
    letter-spacing: 1px;
  }
  .card-back .brand-dot { width: 16px; height: 16px; }
  .social-handle {
    position: absolute;
    left: 0; right: 0; top: 336px;
    text-align: center;
    font-size: 20px; font-weight: 400;
    color: var(--on-dark);
    letter-spacing: 0.4px;
  }
  .social-handle .handle-mark {
    display: inline-block;
    width: 14px; height: 14px;
    border: 2px solid var(--accent);
    border-radius: 50%;
    margin-right: 8px;
    vertical-align: -1px;
  }
</style>
</head>
<body>

<section class="card card-front" aria-label="Card front">
  <div class="brand">
    <span class="brand-name">KESTREL HILL</span>
    <span class="brand-dot"></span>
  </div>

  <div class="divider"></div>

  <div class="contact-block">
    <p class="person-name"><span class="first">DANIEL</span> MARSH</p>
    <ul class="contact-list">
      <li>
        <svg viewBox="0 0 16 16" aria-hidden="true"><path fill="#1f8a3c" d="M3.2 1.5l2.3 2.6-1.3 1.6c.9 2 2.4 3.5 4.3 4.4l1.6-1.3 2.6 2.3-1.4 2.4C6.8 13.4 2.6 9.2 1 4.6z"/></svg>
        0412 555 318
      </li>
      <li>
        <svg viewBox="0 0 16 16" aria-hidden="true"><rect x="1" y="3.5" width="14" height="9" fill="#1f8a3c"/><path d="M1.5 4l6.5 5 6.5-5M1.5 12l5-4M14.5 12l-5-4" stroke="#fff" stroke-width="1.1" fill="none"/></svg>
        info@kestrelhillelectrical.au
      </li>
      <li>
        <svg viewBox="0 0 16 16" aria-hidden="true"><circle cx="8" cy="8" r="7" fill="#1f8a3c"/><path d="M8 1v14M1 8h14M8 1c-3 3.5-3 10.5 0 14M8 1c3 3.5 3 10.5 0 14" stroke="#fff" stroke-width="1" fill="none"/></svg>
        www.kestrelhillelectrical.au
      </li>
    </ul>
    <p class="registration">ABN - 12 345 678 901<br>Lic Number - 418862K</p>
  </div>

  <p class="services">Residential<span class="sep">•</span>Commercial<span class="sep">•</span>Industrial<span class="sep">•</span>24hr Service</p>
</section>

<section class="card card-back" aria-label="Card back">
  <div class="brand">
    <span class="brand-dot"></span>
    <span class="brand-name">KESTREL HILL</span>
  </div>
  <p class="social-handle"><span class="handle-mark"></span>kestrel.hill.electrical</p>
</section>

</body>
</html>
```